VOMRA Pty Ltd Business Card

Looking for a simple yet eye-catching double-sided business card design using my company logo on one side and contact details on the other.

Target Market(s)

Government

Industry/Entity Type

Communication Systems Engineering

Contact Information for Business Card

VOMRA Pty Ltd

Requirements
Nice to have
• Would be great to have a QR code so details can be scanned into contacts

```html
<!DOCTYPE html>
<html lang="en">
<head>
<meta charset="utf-8">
<title>VOMRA Pty Ltd Business Card</title>
<link href="https://fonts.googleapis.com/css2?family=Montserrat:wght@400;500;700&display=swap" rel="stylesheet">
<style>
  :root {
    --bg: #d9dadb;
    --slate-light: #737b80;
    --slate-dark: #36414a;
    --slate-deep: #2f3a42;
    --tab-grey: #454646;
    --ink: #3b444b;
    --ink-soft: #4a5258;
    --paper-top: #ffffff;
    --paper-bottom: #ececec;
    --white: #ffffff;
  }
  * { box-sizing: border-box; margin: 0; padding: 0; }
  html, body { width: 1200px; height: 1200px; overflow: hidden; }
  body {
    background: var(--bg);
    font-family: "Montserrat", sans-serif;
    display: flex;
    flex-direction: column;
    align-items: center;
    justify-content: center;
    gap: 60px;
  }
  .card {
    width: 840px;
    height: 480px;
    border-radius: 34px;
    position: relative;
    overflow: hidden;
    box-shadow: 0 12px 30px rgba(0,0,0,0.18);
  }
  /* Front */
  .card-front {
    background: linear-gradient(100deg, var(--slate-light) 0%, var(--slate-dark) 55%, var(--slate-deep) 100%);
    display: flex;
    align-items: center;
    justify-content: center;
    gap: 28px;
  }
  .brand-dot {
    width: 64px; height: 64px; border-radius: 50%;
    background: var(--white);
  }
  .brand-name-front {
    color: var(--white);
    font-weight: 500;
    font-size: 120px;
    letter-spacing: 2px;
    line-height: 1;
  }
  /* Back */
  .card-back {
    background: linear-gradient(160deg, var(--paper-top) 0%, var(--paper-bottom) 100%);
  }
  .edge-strip { position: absolute; right: 0; width: 30px; background: var(--slate-dark); }
  .edge-top { top: 0; height: 170px; border-bottom-left-radius: 14px; }
  .edge-tab { top: 190px; height: 80px; right: 0; width: 22px; background: var(--tab-grey); border-radius: 10px 0 0 10px; }
  .edge-bottom { bottom: 0; height: 190px; border-top-left-radius: 14px; }
  .back-brand {
    position: absolute; left: 80px; top: 60px;
    display: flex; align-items: center; gap: 18px;
  }
  .back-brand .brand-dot { width: 38px; height: 38px; background: var(--ink); }
  .brand-name-back {
    color: var(--ink); font-weight: 500; font-size: 68px; letter-spacing: 1px; line-height: 1;
  }
  .holder {
    position: absolute; right: 90px; top: 160px; text-align: right;
  }
  .holder-name { font-weight: 700; font-size: 36px; color: var(--slate-deep); }
  .holder-role { font-weight: 400; font-size: 21px; color: var(--ink-soft); margin-top: 4px; }
  .contact {
    position: absolute; left: 80px; bottom: 50px;
    color: var(--ink-soft); font-size: 21px; line-height: 1.4;
  }
  .address { margin-bottom: 8px; }
  .contact-line { display: flex; align-items: center; gap: 14px; }
  .contact-line svg { width: 20px; height: 20px; fill: var(--ink-soft); flex: none; }
</style>
</head>
<body>
  <section class="card card-front">
    <span class="brand-dot"></span>
    <span class="brand-name-front">VOMRA</span>
  </section>

  <section class="card card-back">
    <div class="edge-strip edge-top"></div>
    <div class="edge-strip edge-tab"></div>
    <div class="edge-strip edge-bottom"></div>

    <div class="back-brand">
      <span class="brand-dot"></span>
      <span class="brand-name-back">VOMRA</span>
    </div>

    <div class="holder">
      <div class="holder-name">Daniel Marsh</div>
      <div class="holder-role">Founder &amp; Director</div>
    </div>

    <div class="contact">
      <div class="address">42-44 Harbour Lane Westfield<br>NSW 2150 Australia</div>
      <div class="contact-line">
        <svg viewBox="0 0 24 24" aria-hidden="true"><path d="M6.6 10.8a15.1 15.1 0 0 0 6.6 6.6l2.2-2.2a1 1 0 0 1 1-.25 11.4 11.4 0 0 0 3.6.57 1 1 0 0 1 1 1V20a1 1 0 0 1-1 1A17 17 0 0 1 3 4a1 1 0 0 1 1-1h3.5a1 1 0 0 1 1 1c0 1.25.2 2.45.57 3.57a1 1 0 0 1-.25 1z"/></svg>
        <span>(402)-555-0147</span>
      </div>
      <div class="contact-line">
        <svg viewBox="0 0 24 24" aria-hidden="true"><path d="M2 5h20v14H2z M2 5l10 8 10-8" /></svg>
        <span>admin@vomra.com.au</span>
      </div>
      <div class="contact-line">
        <svg viewBox="0 0 24 24" aria-hidden="true"><path d="M12 2a10 10 0 1 0 0 20 10 10 0 0 0 0-20zm6.9 6h-3a15.7 15.7 0 0 0-1.3-3.9A8 8 0 0 1 18.9 8zM12 4a14 14 0 0 1 1.9 4h-3.8A14 14 0 0 1 12 4zM4.3 14a8 8 0 0 1 0-4h3.4a16 16 0 0 0 0 4zm.8 2h3a15.7 15.7 0 0 0 1.3 3.9A8 8 0 0 1 5.1 16zm3-8h-3a8 8 0 0 1 4.3-3.9A15.7 15.7 0 0 0 8.1 8zM12 20a14 14 0 0 1-1.9-4h3.8A14 14 0 0 1 12 20zm2.3-6H9.7a14 14 0 0 1 0-4h4.6a14 14 0 0 1 0 4zm.3 5.9a15.7 15.7 0 0 0 1.3-3.9h3a8 8 0 0 1-4.3 3.9zm1.7-5.9a16 16 0 0 0 0-4h3.4a8 8 0 0 1 0 4z"/></svg>
        <span>www.vomra.com.au</span>
      </div>
    </div>
  </section>
</body>
</html>
```